Aerial Imaging and photgraphy business card

Design a business card with eye catching aerial photo of country side / landscape with a drone in the foreground.
Also contact details.

Target Market(s)

Aerial Imaging photography

Industry/Entity Type

Advertising

Contact Information for Business Card

Rowland
0412965203
Website http://www.skywardvistaphoto.com.au/
email address : skywardvistaphoto.com.au

Colors
e8f1ca
cadf82
9bcb3c
33a6d7
85cae6
cee9f5

Requirements
Must have
• High res photo
• Korvane drone in the foreground Either T4200 and korvane Glidewing or both
Nice to have
• high resolution landscape country photo on the front of the card with a Korvane T4200 drone in the foreground.

```html
<!DOCTYPE html>
<html lang="en">
<head>
<meta charset="utf-8">
<title>Skyward Vista Photo – Business Card</title>
<link href="https://fonts.googleapis.com/css2?family=Roboto:wght@400;500;700&family=Roboto+Condensed:wght@400;700&display=swap" rel="stylesheet">
<style>
  :root {
    --page-bg: #e9e9e9;
    --card-bg: #ffffff;
    --ink: #3a3a3a;
    --ink-soft: #6b6b6b;
    --green: #7cc427;
    --green-light: #cadf82;
    --teal-dark: #145a70;
    --teal: #1f7f9c;
    --sky: #85cae6;
    --sky-pale: #cee9f5;
    --icon-blue: #2b8fd0;
  }
  * { margin: 0; padding: 0; box-sizing: border-box; }
  html, body { width: 1200px; height: 1200px; overflow: hidden; }
  body {
    background: var(--page-bg);
    font-family: "Roboto", Arial, sans-serif;
    position: relative;
  }
  .card {
    position: absolute;
    left: 250px;
    width: 700px;
    height: 400px;
    border-radius: 14px;
    overflow: hidden;
    box-shadow: 0 8px 22px rgba(0,0,0,0.18);
  }
  .card--front { top: 150px; }
  .card--back { top: 640px; background: var(--card-bg); }

  .front-photo {
    width: 100%;
    height: 100%;
    background: linear-gradient(180deg, #9cc7e6 0%, #d7e6ee 30%, #c9d7cf 45%, #7fa35a 62%, #4c6b36 82%, #35492a 100%);
  }

  .back-shapes { position: absolute; inset: 0; width: 100%; height: 100%; }

  .brand {
    position: absolute;
    left: 56px;
    top: 150px;
    width: 230px;
    display: flex;
    align-items: center;
    gap: 10px;
  }
  .brand-dot {
    width: 18px; height: 18px; border-radius: 50%;
    background: var(--teal);
    flex: none;
  }
  .brand-name {
    font-family: "Roboto Condensed", Arial, sans-serif;
    font-weight: 700;
    font-size: 26px;
    line-height: 1.1;
    color: var(--teal-dark);
    text-transform: uppercase;
  }

  .divider {
    position: absolute;
    left: 318px;
    top: 40px;
    width: 1px;
    height: 190px;
    background: var(--green-light);
  }

  .contact {
    position: absolute;
    left: 356px;
    top: 60px;
    color: var(--ink);
  }
  .contact-name { font-size: 26px; font-weight: 700; letter-spacing: 0.3px; }
  .contact-title { font-size: 15px; color: var(--ink-soft); margin-top: 2px; margin-left: 14px; }
  .contact-list { list-style: none; margin-top: 18px; margin-left: 14px; }
  .contact-list li {
    display: flex; align-items: center; gap: 10px;
    font-family: "Roboto Condensed", Arial, sans-serif;
    font-size: 16px; line-height: 24px;
  }
  .contact-list svg { width: 14px; height: 14px; flex: none; }

  .website {
    position: absolute;
    right: 34px;
    bottom: 40px;
    font-family: "Roboto Condensed", Arial, sans-serif;
    font-size: 15px;
    color: #ffffff;
    letter-spacing: 0.3px;
  }
</style>
</head>
<body>

<section class="card card--front">
  <div class="front-photo" role="img" aria-label="Aerial photo of green countryside and a lake with a camera drone flying in the foreground"></div>
</section>

<section class="card card--back">
  <svg class="back-shapes" viewBox="0 0 700 400" preserveAspectRatio="none" aria-hidden="true">
    <defs>
      <linearGradient id="tealBand" x1="0" y1="0" x2="1" y2="0">
        <stop offset="0" stop-color="#0f4f63"/>
        <stop offset="0.5" stop-color="#1b7c9a"/>
        <stop offset="1" stop-color="#145a70"/>
      </linearGradient>
    </defs>
    <polygon points="0,390 465,372 465,400 0,400" fill="#7cc427"/>
    <polygon points="460,305 700,262 700,400 468,400" fill="url(#tealBand)"/>
  </svg>

  <div class="brand">
    <span class="brand-dot"></span>
    <span class="brand-name">Skyward Vista Photo</span>
  </div>

  <div class="divider"></div>

  <div class="contact">
    <div class="contact-name">Liam Rowland</div>
    <div class="contact-title">Managing Director</div>
    <ul class="contact-list">
      <li>
        <svg viewBox="0 0 16 16"><path fill="#2b8fd0" d="M3 1h3l1.5 4-2 1.2a9 9 0 0 0 4.3 4.3L11 8.5l4 1.5v3a2 2 0 0 1-2 2A13 13 0 0 1 1 3a2 2 0 0 1 2-2z"/></svg>
        0412965203
      </li>
      <li>
        <svg viewBox="0 0 16 16"><rect x="1" y="3" width="14" height="10" rx="1.5" fill="#2b8fd0"/><path d="M1.5 4l6.5 5 6.5-5" stroke="#fff" stroke-width="1.3" fill="none"/></svg>
        hello@skywardvistaphoto.com.au
      </li>
      <li>
        <svg viewBox="0 0 16 16"><path fill="#2b8fd0" d="M8 0a5.5 5.5 0 0 0-5.5 5.5C2.5 10 8 16 8 16s5.5-6 5.5-10.5A5.5 5.5 0 0 0 8 0z"/><circle cx="8" cy="5.5" r="2" fill="#fff"/></svg>
        Ridgevale NSW 2590, Australia
      </li>
    </ul>
  </div>

  <div class="website">www.skywardvistaphoto.com.au</div>
</section>

</body>
</html>
```